Residential Mortgage Leader needs Wordpress Design

Looking for a home page website design for a client. We develop using the WordPress platform and would prefer the design be at least loosely based on an existing WordPress template. Attached files have many notes from our creative brief with client. The site must be responsive. Approved, basic wireframe attached. There is room for interpretation.

Existing web site: http://www.marisolkettering.example/

The Marisol Kettering Team relies on strong systems to deliver an on-time, done-right, friendly experience. Marisol offers mortgages and refinancing services throughout the United States. She is a successful Brookvale Funding agent who strives to be an active part of her community. She would like to focus the site on her team, rather than just her.

Difference makers...
When you work with the Marisol Kettering team you get a high level of expertise and a friendly experience.

She has amazing credentials. Marisol is widely recognized as a top producer for her company, and has earned a number of awards and honors for her customer service.

Marisol's team is very engaged and enjoys sharing social comments or photos from their community.

Imagery:
* Friendly, warm imagery, preferably of her team or an image to represent her team
* Clean and crisp
* Professional / Experts in mortgage and refinance
* Clean / Good use of white space
Updates

When possible, please use imagery from the DFW area. The client mentioned they would prefer not to see stock images. Thanks.

Amend that- creative use of stock images, however, is fine. A few designs have used stock imagery, but in a well-considered manner.

We added some photos and graphics that are local. We are Dallas / Ft. Worth, Plano, Frisco, Texas. We also added some examples of photos to use for the "In the Community" area. Stock photos of business folks just doesn't fit there. Thanks!

Target Market(s)

They service a lot of builders, but also work with homeowners. Their typical client is usually a woman searching for mortgage services online. She typically has a family and may refer her husband to Marisol's team. Keep in mind, however, they also see a number of other scenarios. Most of their clients are middle to high-end borrowers.

Industry/Entity Type

It Company

Requirements
Must have
• Design should be developed using program such as Photoshop or Fireworks or Illustrator as last preference. Ideally, the design would be based on an existing responsive WordPress theme, which we would customize. You must include the name of the target theme. The footer should include lots of space for disclaimers and legal language. Site navigation should include these choices: "Home, About, Builders, Mortgage Info, Approval, Blog, Contact"
Nice to have
• Blog, social media and photos area. Use of the already approved style prototype with colors and fonts (Lato- a Google font, Times New Roman and Cookie-a decorative Google font). However, we are open to interpretation.
Should not have
• Hard to read fonts or a lack of white space.

```html
<!DOCTYPE html>
<html lang="en">
<head>
<meta charset="utf-8">
<title>Marisol Kettering Team | Brookvale Funding</title>
<link rel="stylesheet" href="https://fonts.googleapis.com/css2?family=Lato:ital,wght@0,400;0,700;1,400&family=Cookie&display=swap">
<style>
:root{
  --red:#c8321f;
  --red-dark:#a82818;
  --charcoal:#333333;
  --panel:#3a3a3a;
  --text:#555555;
  --heading:#1f1f1f;
  --rule:#e2e2e2;
  --hero-top:#9a9a9a;
  --hero-mid:#d8d8d8;
  --hero-bottom:#f2f2f2;
  --page:#ffffff;
  --footer:#f3f3f3;
}
*{margin:0;padding:0;box-sizing:border-box}
html,body{width:881px;height:1200px;overflow:hidden}
body{position:relative;background:var(--page);font-family:"Lato",sans-serif;color:var(--text)}
.abs{position:absolute}
.hero{left:0;top:0;width:881px;height:456px;background:linear-gradient(180deg,var(--hero-top) 0%,var(--hero-mid) 35%,#bdbdbd 60%,var(--hero-bottom) 100%)}
.brand{left:84px;top:30px}
.brand-name{font-size:31px;font-weight:700;color:var(--red);letter-spacing:-0.5px;line-height:1}
.brand-tag{font-size:15px;color:#555;margin-top:6px}
.brand-mark{left:312px;top:14px;width:26px;height:26px;border-radius:50%;background:var(--red)}
.contact-top{right:88px;top:26px;text-align:right;color:var(--red)}
.contact-top .phone{font-size:22px;letter-spacing:.5px}
.contact-top .email{font-size:11px;margin-top:4px}
.nav{left:74px;top:100px;width:734px;height:39px;background:var(--red);display:flex;align-items:center}
.nav a{color:#fff;text-decoration:none;font-size:13px;padding:0 14px;height:39px;line-height:39px}
.nav a.active{background:var(--charcoal);padding:0 12px;margin-right:4px}
.team-mark{right:80px;top:146px;text-align:right}
.team-mark .name{font-size:32px;color:#7a1f1a;letter-spacing:-0.5px;line-height:1}
.team-mark .sub{font-size:9.5px;color:#666;letter-spacing:.6px;margin-top:2px}
.collage{left:82px;top:155px;width:325px;height:290px}
.slide-btn{top:397px;width:21px;height:21px;border-radius:50%;background:#444}
.hero-panel{left:446px;top:228px;width:335px;height:189px;background:rgba(45,45,45,.92);color:#fff;padding:22px 30px}
.hero-panel h1{font-family:"Cookie",cursive;font-weight:400;font-size:34px;line-height:1}
.hero-panel p{font-size:14px;line-height:18px;margin-top:10px;width:260px}
.btn{display:inline-block;height:25px;line-height:25px;font-size:14px;color:#fff;border-radius:2px;padding:0 18px}
.btn-red{background:var(--red)}
.btn-grey{background:#6e6e6e}
.actions{margin-top:28px;display:flex;align-items:center;gap:12px;margin-left:-2px}
.actions .or{font-size:13px}
.section-title{font-size:21px;color:var(--heading);font-weight:400}
.kicker{font-size:11.5px;color:var(--red)}
.body-copy{font-size:9.5px;line-height:12.4px;color:var(--text)}
.col-div{width:1px;background:linear-gradient(180deg,#fff,#e6e6e6 40%,#fff)}
.side-tab{left:0;top:567px;width:47px;height:222px;background:var(--charcoal);border-radius:0 4px 4px 0}
.side-tab .dot{position:absolute;left:10px;top:9px;width:22px;height:12px;border-radius:50%;background:var(--red)}
.side-tab span{position:absolute;left:13px;top:34px;writing-mode:vertical-rl;color:#fff;font-size:13px;white-space:nowrap}
.post-title{font-size:11.5px;font-style:italic;color:var(--red);line-height:14px}
.date{width:46px;height:57px;background:var(--charcoal);color:#fff;text-align:center;font-size:9px;padding-top:4px;line-height:1.1}
.date b{display:block;font-size:19px;font-weight:400;margin:2px 0}
.date i{font-size:10px}
.social-sq{top:822px;width:23px;height:23px}
.community-box{left:568px;top:727px;width:230px;height:159px;background:var(--panel)}
.thumb{width:80px;height:57px;border:2px solid #fff}
.community-box p{position:absolute;left:107px;width:108px;font-size:9.2px;line-height:13.4px;color:#eee;text-align:justify}
.footer{left:0;top:917px;width:881px;height:283px;background:linear-gradient(180deg,#fff,var(--footer));border-top:1px solid var(--rule)}
.foot-h{font-size:17.5px;color:var(--heading)}
.foot-copy{font-size:9.6px;line-height:13.3px;color:var(--text)}
.portrait{left:84px;top:953px;width:74px;height:83px;border:3px solid #fff;box-shadow:0 0 3px rgba(0,0,0,.25);background:linear-gradient(160deg,#8a5a46,#3a2a24)}
.eho{left:733px;top:988px;width:66px;height:68px}
.foot-nav{left:87px;top:1121px;display:flex;gap:22px;font-size:9.8px;color:#333}
.copyright{right:95px;top:1154px;font-size:9.6px;color:#333}
</style>
</head>
<body>

<header>
  <div class="abs hero"></div>
  <div class="abs brand">
    <div class="brand-name">Brookvale Funding</div>
    <div class="brand-tag">A Hollowmere Capital Company</div>
  </div>
  <div class="abs contact-top">
    <div class="phone">123 - 456 - 7890</div>
    <div class="email">Email : info@brookvalefunding.example</div>
  </div>
  <nav class="abs nav">
    <a class="active">Home</a><a>About Us</a><a>Business</a><a>Manage info</a><a>Approval</a><a>Blog</a><a>Contact Us</a>
  </nav>
</header>

<section class="hero-content">
  <div class="abs team-mark">
    <div class="name">marisolkettering</div>
    <div class="sub">THE MARISOL KETTERING TEAM</div>
  </div>

  <svg class="abs collage" viewBox="0 0 325 290" role="img" aria-label="Collage of three local Frisco area photographs: a historic rail depot, a ballpark and a retail store">
    <g transform="translate(26,5)">
      <rect width="180" height="120" fill="#fff"/>
      <rect x="4" y="4" width="172" height="112" fill="#b9714f"/>
      <rect x="4" y="4" width="172" height="50" fill="#8fb2d6"/>
    </g>
    <g transform="translate(170,55) rotate(-22)">
      <rect width="165" height="140" fill="#fff"/>
      <rect x="5" y="5" width="155" height="130" fill="#8c9aa8"/>
      <rect x="5" y="5" width="155" height="50" fill="#c5d4e2"/>
    </g>
    <g transform="translate(60,120) rotate(24)">
      <rect width="190" height="135" fill="#fff"/>
      <rect x="5" y="5" width="180" height="125" fill="#7f8a8f"/>
      <rect x="5" y="5" width="180" height="55" fill="#2e55a8"/>
    </g>
  </svg>
  <div class="abs slide-btn" style="left:91px"></div>
  <div class="abs slide-btn" style="left:118px"></div>
  <svg class="abs" style="left:91px;top:397px" width="48" height="21" viewBox="0 0 48 21" aria-hidden="true">
    <path d="M13 6 L7 10.5 L13 15 Z" fill="#fff"/>
    <path d="M35 6 L41 10.5 L35 15 Z" fill="#fff"/>
  </svg>

  <div class="abs hero-panel">
    <h1>Earning Your Business</h1>
    <p>The Marisol Kettering Team relies on strong systems to deliver an on-time, done-right and friendly experience</p>
    <div class="actions">
      <span class="btn btn-red">Start here</span>
      <span class="or">(Or)</span>
      <span class="btn btn-grey">Get to know us</span>
    </div>
  </div>
</section>

<section class="highlights">
  <div class="abs" style="left:84px;top:480px;width:265px">
    <h2 class="section-title">Our Credentials</h2>
    <div class="kicker" style="margin-top:8px">A top-producer , top-notch</div>
    <p class="body-copy" style="margin-top:11px">Marisol has been a Brookvale Power Producer for the last 7 years. This means she has earned top awards for her service and expertise. Find out why the Marisol Kettering team stands out from the rest!</p>
  </div>
  <div class="abs col-div" style="left:366px;top:460px;height:140px"></div>
  <div class="abs" style="left:383px;top:479px;width:190px">
    <h2 class="section-title">Awards</h2>
    <p class="body-copy" style="margin-top:8px">Marisol was also ranked #42 in the nation in Lender Review Monthly in 2008 and in 2009 was ranked #63 in the nation in Harlow Guide Top 200. Marisol has been in the top 5 producers for Brookvale Funding over the last 4 years.</p>
  </div>
  <div class="abs col-div" style="left:590px;top:460px;height:140px"></div>
  <div class="abs" style="left:606px;top:479px;width:192px">
    <h2 class="section-title">Recognition</h2>
    <p class="body-copy" style="margin-top:8px;text-align:justify">"I worked with Marisol's team last year and couldn't be happier! The experience was totally unique. They were very knowledgeable and friendly, but what stood out to me the most was that we closed on time without any hiccups!"</p>
    <div class="kicker" style="font-size:9.6px;text-align:right;margin-top:5px">Jane Smith, Frisco</div>
  </div>
  <div class="abs" style="left:0;top:615px;width:881px;height:1px;background:var(--rule)"></div>
</section>

<aside class="abs side-tab"><div class="dot"></div><span>Mortgages without obstacles</span></aside>

<section class="community">
  <h2 class="abs section-title" style="left:0;width:881px;text-align:center;top:635px">Engaged in our Community</h2>
  <div class="abs kicker" style="left:0;width:881px;text-align:center;top:666px">Connect with us</div>

  <div class="abs" style="left:85px;top:700px;width:215px">
    <h3 class="section-title" style="font-size:18px">Recent Posts</h3>
  </div>
  <div class="abs" style="left:87px;top:730px;width:155px">
    <div class="post-title">Lorem Ipsum is simply dummy text of the printing</div>
    <p class="body-copy" style="margin-top:6px;text-align:justify">Sed ut perspiciatis unde omnis iste natus error sit voluptatem accusantium doloremque</p>
  </div>
  <div class="abs date" style="left:252px;top:733px">2013<b>06</b><i>Sep</i></div>
  <div class="abs" style="left:87px;top:811px;width:155px">
    <div class="post-title">Lorem Ipsum is simply dummy text of the printing</div>
    <p class="body-copy" style="margin-top:6px;text-align:justify">Sed ut perspiciatis unde omnis iste natus error sit voluptatem accusantium doloremque</p>
  </div>
  <div class="abs date" style="left:252px;top:815px">2013<b>06</b><i>Sep</i></div>

  <div class="abs col-div" style="left:312px;top:695px;height:180px"></div>
  <div class="abs" style="left:328px;top:700px;width:200px">
    <h3 class="section-title" style="font-size:18px">Social</h3>
    <p class="body-copy" style="margin-top:18px;font-size:8.8px;line-height:13.3px;text-align:justify">"Marisol specializes in putting her "personal touch" on each loan that comes to her desk, and values communicating with current and future clients. Connect with the team today!</p>
  </div>
  <div class="abs social-sq" style="left:422px;background:#1e4f9c"></div>
  <div class="abs social-sq" style="left:452px;background:#3aa3dd"></div>
  <div class="abs social-sq" style="left:481px;background:#555"></div>
  <div class="abs social-sq" style="left:510px;background:#e89a1c"></div>

  <div class="abs col-div" style="left:551px;top:695px;height:180px"></div>
  <h3 class="abs section-title" style="left:566px;top:697px;font-size:18px">In the community</h3>
  <div class="abs community-box">
    <div class="abs thumb" role="img" aria-label="Family standing by a sold home sign" style="left:13px;top:17px;background:linear-gradient(180deg,#7a8f6a,#b58a6e)"></div>
    <p style="top:20px">Sed ut perspiciatis unde omnis iste natus error sit voluptatem accusantium doloremque</p>
    <div class="abs thumb" role="img" aria-label="Local civic building exterior" style="left:13px;top:87px;background:linear-gradient(180deg,#d9dde2,#a48a72)"></div>
    <p style="top:88px">Sed ut perspiciatis unde omnis iste natus error sit voluptatem accusantium doloremque</p>
  </div>
</section>

<footer>
  <div class="abs footer"></div>
  <div class="abs" style="left:90px;top:933px;font-size:11px;color:#222">Marisol Kettering</div>
  <div class="abs portrait" role="img" aria-label="Portrait of Marisol Kettering"></div>
  <div class="abs foot-copy" style="left:174px;top:959px">Office: 469.555.0142<br>Cell: 866.555.0187<br>mkettering@brookvalefunding.example<br><br>4280 Larkspur Commons , Ste. 210<br>Frisco, TX 75034</div>
  <div class="abs foot-copy" style="left:88px;top:1060px;color:#333">Branch Manager<br>NMLS #: 40518</div>

  <div class="abs" style="left:338px;top:943px;width:185px">
    <div class="foot-h">Head office</div>
    <p class="foot-copy" style="margin-top:8px">Our Address<br>Corporate Office - 9020 Wexford Road, Suite 700 Dallas, Texas 75252<br>Tel : 1-800-555-0163<br>Email : Contact Brookvale Funding</p>
  </div>
  <div class="abs" style="left:537px;top:943px;width:185px">
    <div class="foot-h">Branch Office</div>
    <p class="foot-copy" style="margin-top:8px">Our Address<br>Larkspur Commons - 4280 Larkspur Commons , Ste. 210 • Frisco, TX 75034<br>Tel : 469.555.0142<br>Fax : 866.555.0187<br>Email : Contact Marisol Kettering</p>
  </div>
  <svg class="abs eho" viewBox="0 0 66 68" role="img" aria-label="Housing compliance badge">
    <rect x="8" y="8" width="50" height="50" fill="none" stroke="#7a7a7a" stroke-width="5"/>
  </svg>
  <div class="abs foot-copy" style="left:819px;top:1059px;color:#333">M1</div>

  <nav class="abs foot-nav"><span>Home</span><span>About Us</span><span>Business</span><span>Manage info</span><span>Approval</span><span>Blog</span><span>Contact Us</span></nav>
  <div class="abs copyright">© 2013.www.brookvalefunding.example</div>
</footer>

</body>
</html>
```